Sparrow Haulage needs a business card design.

Design a double-sided business card for new freight business. On the front, would like to see our logo along with the following info:

Martin Obuya
CEO/FOUNDER
555-206-7142
martinobuya@sparrow-haulage.example

On the reverse side, we would like to use the graphic image of our logo only without the Sparrow Haulage name.

```html
<!DOCTYPE html>
<html lang="en">
<head>
<meta charset="utf-8">
<title>Sparrow Haulage — Business Card</title>
<link rel="stylesheet" href="https://fonts.googleapis.com/css2?family=Roboto:wght@400;700;900&display=swap">
<style>
  :root {
    --navy: #0b0f5c;
    --navy-deep: #04034f;
    --red: #c20a0a;
    --icon-red: #e0080e;
    --ink: #2b2b2b;
    --rule: #8a8a8a;
    --paper: #ffffff;
    --stage: #b9b9b9;
  }
  * { margin: 0; padding: 0; box-sizing: border-box; }
  html, body {
    width: 1200px; height: 1200px; overflow: hidden;
    background: var(--stage);
    font-family: "Roboto", Arial, sans-serif;
  }
  .card {
    position: absolute;
    width: 364px; height: 588px;
    border-radius: 16px;
    overflow: hidden;
  }
  .card-back {
    left: 203px; top: 307px;
    background: var(--navy-deep);
  }
  .back-pattern {
    position: absolute; inset: 0;
    background: radial-gradient(ellipse at 50% 45%, #0c0ca0 0%, #07067a 45%, var(--navy-deep) 85%);
  }
  .back-mark {
    position: absolute; left: 207px; top: 412px;
    width: 52px; height: 52px;
    background: var(--red);
  }

  .card-front {
    left: 601px; top: 306px;
    background: var(--paper);
  }
  .brand {
    position: absolute; left: 0; right: 0; top: 160px;
    display: flex; align-items: center; justify-content: center; gap: 10px;
    color: var(--navy);
    font-weight: 700; font-size: 25px; letter-spacing: 2.5px; text-transform: uppercase;
  }
  .brand .square { width: 18px; height: 18px; background: var(--red); }
  .contact {
    position: absolute; left: 0; right: 0; top: 372px;
    text-align: center;
  }
  .person-name { font-weight: 900; font-size: 22px; letter-spacing: 0.2px; }
  .person-name .first { color: var(--navy); }
  .person-name .last { color: var(--red); }
  .person-role { margin-top: 2px; font-size: 17px; color: var(--ink); }
  .icon-row {
    margin-top: 14px;
    display: flex; align-items: center; justify-content: center; gap: 5px;
  }
  .icon-row .rule { width: 52px; height: 1px; background: var(--rule); margin: 0 4px; }
  .icon-row .icon {
    width: 25px; height: 25px; border-radius: 3px; background: var(--icon-red);
    display: flex; align-items: center; justify-content: center;
  }
  .details { margin-top: 12px; font-size: 15.5px; line-height: 22px; color: var(--ink); }
  .details .web .navy { color: var(--navy); }
  .details .web .red { color: var(--red); }
</style>
</head>
<body>
  <section class="card card-back">
    <div class="back-pattern" role="img" aria-label="Faint repeating brand pattern in deep blue"></div>
    <div class="back-mark" role="img" aria-label="Company mark"></div>
  </section>

  <section class="card card-front">
    <div class="brand"><span class="square"></span>Sparrow Haulage</div>

    <div class="contact">
      <div class="person-name"><span class="first">MARTIN</span> <span class="last">OBUYA</span></div>
      <div class="person-role">CEO/FOUNDER</div>

      <div class="icon-row">
        <span class="rule"></span>
        <span class="icon" aria-label="Phone">
          <svg width="15" height="15" viewBox="0 0 24 24" fill="#fff"><path d="M6.6 10.8a15 15 0 0 0 6.6 6.6l2.2-2.2a1 1 0 0 1 1-.25 11.4 11.4 0 0 0 3.6.57 1 1 0 0 1 1 1V20a1 1 0 0 1-1 1A17 17 0 0 1 3 4a1 1 0 0 1 1-1h3.5a1 1 0 0 1 1 1c0 1.25.2 2.45.57 3.57a1 1 0 0 1-.25 1z"/></svg>
        </span>
        <span class="icon" aria-label="Email">
          <svg width="16" height="12" viewBox="0 0 16 12" fill="none" stroke="#fff" stroke-width="1.3"><rect x="1" y="1" width="14" height="10"/><path d="M1 1l7 6 7-6M1 11l5-4.5M15 11l-5-4.5"/></svg>
        </span>
        <span class="icon" aria-label="Website">
          <svg width="15" height="15" viewBox="0 0 16 16" fill="none" stroke="#fff" stroke-width="1.3"><circle cx="8" cy="8" r="6.5"/><path d="M1.5 8h13M8 1.5c2 2 2 11 0 13M8 1.5c-2 2-2 11 0 13"/></svg>
        </span>
        <span class="rule"></span>
      </div>

      <div class="details">
        <div>555-206-7142</div>
        <div>martinobuya@sparrow-haulage.example</div>
        <div class="web">www.<span class="navy">sparrow</span>-<span class="red">haulage</span>.example</div>
      </div>
    </div>
  </section>
</body>
</html>
```